I need a business card design for a new business based in South West Australia.
I specialize in residential window cleaning & general handyman maintenance.

Dale Marsh - 412 SILVER HAWK DETAILING
- Window Cleaning
- House Maintenance

```html
<!DOCTYPE html>
<html lang="en">
<head>
<meta charset="utf-8">
<title>412 Silver Hawk Detailing – Business Card</title>
<link rel="stylesheet" href="https://fonts.googleapis.com/css2?family=Open+Sans:wght@400;600&display=swap">
<style>
  :root {
    --stage: #2e2826;
    --card-dark: #1c1c1d;
    --card-dark-edge: #262627;
    --card-blue: #2a5190;
    --accent: #4a8fdc;
    --pale: #c3d3ee;
    --ink-light: #f2f2f2;
    --ink-soft: #d4d4d4;
    --ink-muted: #a9a9a9;
    --divider: #3a3a3b;
  }
  * { box-sizing: border-box; margin: 0; padding: 0; }
  html, body { width: 1200px; height: 844px; overflow: hidden; }
  body {
    background: var(--stage);
    font-family: "Open Sans", Arial, sans-serif;
    position: relative;
  }
  .card {
    position: absolute;
    top: 272px;
    width: 525px;
    height: 300px;
    border-radius: 3px;
    box-shadow: 0 10px 24px rgba(0,0,0,.45);
    overflow: hidden;
  }
  .card--front {
    left: 50px;
    background: linear-gradient(135deg, var(--card-dark) 0%, var(--card-dark-edge) 100%);
  }
  .card--back {
    left: 625px;
    background: var(--card-blue);
    display: flex;
    flex-direction: column;
    align-items: center;
    justify-content: center;
  }
  .brand {
    position: absolute;
    left: 20px;
    top: 122px;
    width: 262px;
    text-align: center;
  }
  .brand__row {
    display: flex;
    align-items: center;
    justify-content: center;
    gap: 8px;
  }
  .brand__mark {
    width: 12px; height: 12px;
    border-radius: 50%;
    background: var(--accent);
    flex: none;
  }
  .brand__name {
    font-weight: 600;
    font-size: 18px;
    color: var(--ink-light);
    white-space: nowrap;
  }
  .brand__tagline {
    margin-top: 5px;
    font-weight: 400;
    font-size: 11px;
    letter-spacing: .4px;
    color: var(--ink-muted);
    white-space: nowrap;
  }
  .divider {
    position: absolute;
    left: 298px;
    top: 40px;
    width: 1px;
    height: 220px;
    background: var(--divider);
  }
  .contact {
    position: absolute;
    left: 318px;
    top: 58px;
    color: var(--ink-soft);
    font-size: 12.5px;
    line-height: 1.35;
  }
  .contact__name {
    font-weight: 600;
    font-size: 15px;
    color: var(--ink-light);
  }
  .contact__role { margin-bottom: 16px; }
  .contact__address { margin-bottom: 14px; }
  .contact__list { list-style: none; }
  .contact__item {
    display: flex;
    align-items: center;
    gap: 8px;
  }
  .contact__icon { width: 10px; height: 10px; flex: none; fill: var(--ink-soft); }
  .back__row {
    display: flex;
    align-items: center;
    gap: 12px;
  }
  .back__mark {
    width: 18px; height: 18px;
    border-radius: 50%;
    background: var(--pale);
    flex: none;
  }
  .back__name {
    font-weight: 600;
    font-size: 28px;
    color: var(--pale);
    white-space: nowrap;
  }
  .back__tagline {
    margin-top: 8px;
    font-weight: 400;
    font-size: 14px;
    letter-spacing: .5px;
    color: var(--pale);
    white-space: nowrap;
  }
</style>
</head>
<body>

<section class="card card--front" aria-label="Business card front">
  <div class="brand">
    <div class="brand__row">
      <span class="brand__mark"></span>
      <span class="brand__name">412 Silver Hawk Detailing</span>
    </div>
    <div class="brand__tagline">Windows · Repairs · Home Care</div>
  </div>

  <div class="divider"></div>

  <div class="contact">
    <div class="contact__name">Dale Marsh</div>
    <div class="contact__role">Managing Director</div>
    <div class="contact__address">27 Karri Ridge Lane<br>Wattlebrook, 0000.</div>
    <ul class="contact__list">
      <li class="contact__item">
        <svg class="contact__icon" viewBox="0 0 10 10" aria-hidden="true"><path d="M2 0.5 L3.6 0.5 L4.2 2.8 L3 3.6 Q4 5.8 6.4 7 L7.2 5.8 L9.5 6.4 L9.5 8 Q9.5 9.5 8 9.5 Q0.5 8.5 0.5 2 Q0.5 0.5 2 0.5Z"/></svg>
        <span>000-555 0192</span>
      </li>
      <li class="contact__item">
        <svg class="contact__icon" viewBox="0 0 10 10" aria-hidden="true"><path d="M0.5 2 H9.5 V8.5 H0.5Z M0.5 2 L5 5.5 L9.5 2" fill="none" stroke="#d4d4d4" stroke-width="1"/></svg>
        <span>hello@412silverhawk.com</span>
      </li>
      <li class="contact__item">
        <svg class="contact__icon" viewBox="0 0 10 10" aria-hidden="true"><path d="M4 6 L6 4 M3.5 4.5 L2 6 Q1 7.5 2.3 8 Q3 8.8 4 8 L5.5 6.5 M4.5 3.5 L6 2 Q7.5 1 8 2.3 Q8.8 3 8 4 L6.5 5.5" fill="none" stroke="#d4d4d4" stroke-width="1.1" stroke-linecap="round"/></svg>
        <span>www.412silverhawk.com</span>
      </li>
    </ul>
  </div>
</section>

<section class="card card--back" aria-label="Business card back">
  <div class="back__row">
    <span class="back__mark"></span>
    <span class="back__name">412 Silver Hawk Detailing</span>
  </div>
  <div class="back__tagline">Windows · Repairs · Home Care</div>
</section>

</body>
</html>
```